Updated website design needed for Radiology Group, Pine Hollow Imaging Partners

Clean, uncluttered, updated design needed for top regional Radiology Center. Focus on personal, patient oriented design, (not clinical). Should be simple and easy to navigate, with clear CTAs. Use blues, greens and photos of people in the Central Oregon outdoors.
Uncoded, PSD design only. 2 pages: Home page and one example interior page.
reference current site: http://www.phipclinic-example.com/
Sites they like:
http://www.valescanlabs-example.com/
http://www.tbmx-example.net/handler.cfm?event=practice,main
http://www.kestrelbonecare-example.com/

Medical Imaging

2 page

Sans Serif

• Personal and patient friendly.
• Lots of white space, clean and uncluttered. Clear CTAs, such as: Patient Bill Pay, Make an Appointment, Meet Our Doctors
• Use copy and contact information from the current site.
• Use outdoor images from Central Oregon, late Winter/ Spring (snow, light colors, spring green, for example)
• Include one example interior page, either Your Exam or Meet Our Doctors
• The client likes:
• Meet Our Doctors slider section, and big, easy to navigate Information Center on www.kestrelbonecare-example.com
• The personal feel of the Your Exam section on www.valescanlabs-example.com
• Blues and Greens, outdoorsy imagery
• The client does not like:
• complex drop down menus
• clinical feel
• Do not use lorum ipsum or dummy text.
• Do not use outdoor images from other regions. Do not use Summer (hot, poolside) or Fall (red/orange leaves) images.

```html
<!DOCTYPE html>
<html lang="en">
<head>
<meta charset="utf-8">
<title>Pine Hollow Imaging Partners</title>
<link href="https://fonts.googleapis.com/css2?family=Montserrat:wght@600;700&family=Open+Sans:wght@400;600;700&family=Raleway:wght@500;600&display=swap" rel="stylesheet">
<style>
:root{
  --brand:#3d7ea6;
  --brand-deep:#336f95;
  --accent:#5f9a45;
  --ink:#222;
  --dark:#1b2226;
  --dark-band:#1f2629;
  --muted:#8a8a8a;
  --footer-bg:#f2f5f4;
  --white:#fff;
}
*{margin:0;padding:0;box-sizing:border-box}
html,body{width:1200px;height:2476px;overflow:hidden}
body{position:relative;font-family:"Open Sans",Arial,sans-serif;color:var(--ink);background:var(--white)}
.abs{position:absolute}

/* header */
.site-header{left:0;top:0;width:1200px;height:107px;background:var(--white)}
.brand{left:46px;top:14px;display:flex;align-items:center;gap:12px}
.brand-mark{width:66px;height:66px;border:3px solid var(--brand);background:#e4eef4}
.brand-name{font-weight:600;font-size:21px;line-height:24px;color:#244c66;width:170px}
.contact-box{top:25px;height:56px;background:var(--brand);color:var(--white);padding:6px 0 0 22px;white-space:nowrap}
.contact-box b{display:block;font-weight:400;font-size:16.5px;line-height:22px}
.contact-box span{display:flex;align-items:center;gap:4px;font-size:12.5px;margin-top:2px}

/* nav */
.main-nav{left:0;top:107px;width:1200px;height:63px;background:var(--dark);display:flex;align-items:center;padding-left:46px}
.main-nav a{color:var(--white);text-decoration:none;font-size:13.5px;height:63px;line-height:63px;padding:0 20px;position:relative}
.main-nav a.active{background:var(--brand)}
.main-nav a+a::before{content:"|";position:absolute;left:-3px;color:#bbb}
.main-nav a.active+a::before{content:none}

/* hero */
.hero{left:0;top:170px;width:1200px;height:564px;background:linear-gradient(180deg,#9cc3df 0%,#d4e6f1 32%,#f4f7f8 52%,#dfe9e2 68%,#9cbf83 86%,#5f8a4f 100%)}
.hero-panel{left:488px;top:284px;width:712px;height:322px;background:rgba(24,36,44,.72);padding:26px 46px 0 18px;color:var(--white)}
.hero-panel h1{font-family:"Montserrat",sans-serif;font-weight:700;font-size:42px;line-height:54px;letter-spacing:2px;text-align:right}
.hero-panel p{font-size:13.5px;line-height:23px;text-align:right;margin-top:18px}
.btn{display:inline-block;background:var(--accent);color:var(--white);text-decoration:none;font-size:12.5px;text-align:center}
.hero-btn{left:1030px;top:535px;width:126px;height:44px;line-height:44px}
.dots{left:542px;top:578px;display:flex;gap:8px}
.dots i{width:14px;height:14px;border:1.5px solid #ddd;border-radius:50%}
.dots i.on{background:#fff}

/* quick actions */
.actions{left:0;top:734px;width:1200px;height:139px;background:var(--dark-band);display:flex}
.action{width:171.4px;position:relative;text-align:center;color:var(--white);font-weight:700;font-size:18px;line-height:21px;padding-top:54px}
.action+.action{border-left:1px solid #333}
.action-icon{position:absolute;left:50%;top:-42px;margin-left:-43px;width:86px;height:86px;border-radius:50%;background:var(--brand);border:3px solid #e8f0f3;box-shadow:0 0 0 4px rgba(255,255,255,.35);display:flex;align-items:center;justify-content:center}

/* welcome */
.welcome{left:0;top:873px;width:1200px;height:251px;text-align:center}
.welcome h2{font-family:"Raleway",sans-serif;font-weight:500;font-size:32px;margin-top:31px}
.welcome h2 em{font-style:normal;color:var(--brand)}
.welcome p{width:980px;margin:20px auto 0;font-size:12px;line-height:22px;color:var(--muted)}
.welcome .btn{margin-top:24px;width:122px;height:38px;line-height:38px;font-size:11.5px}

/* services */
.services{left:0;top:1124px;width:1200px;height:617px;background:linear-gradient(180deg,#131a17,#22302a 55%,#161d1a)}
.section-title{font-family:"Raleway",sans-serif;font-weight:600;font-size:28px;text-align:center}
.services .section-title{position:absolute;top:38px;width:1200px;color:var(--white)}
.services .section-title em{font-style:normal;color:#7fb2d4}
.service{width:342px;color:var(--white)}
.service h3{font-weight:400;font-size:21px;line-height:28px}
.service p{font-size:11.5px;line-height:20px;color:#ddd;margin-top:4px}
.service a{display:inline-block;font-size:11px;margin-top:6px;text-decoration:none}
.service.left{left:90px;text-align:right}
.service.left a{color:var(--white)}
.service.right{left:764px}
.service.right a{color:#7fb2d4}
.service-photo{width:112px;height:112px;border-radius:50%;border:3px solid var(--white)}
.spine{left:595px;top:1286px;width:2px;height:316px;background:#cfcfcf}
.spine-h{height:2px;background:#cfcfcf;left:554px;width:84px}

/* testimonials */
.testimonials{left:0;top:1741px;width:1200px;height:358px;background:var(--brand-deep);color:var(--white);text-align:center}
.testimonials .section-title{font-family:"Open Sans",sans-serif;font-weight:600;font-size:34px;margin-top:55px}
.quote{width:820px;margin:22px auto 0;font-size:13px;line-height:27px}
.quote .mark{font-family:Georgia,serif;font-size:40px;line-height:0;vertical-align:-12px}
.author{font-size:16px;margin-top:14px;letter-spacing:.5px}
.avatars{display:flex;justify-content:center;gap:14px;margin-top:30px}
.avatar{width:72px;height:72px;border-radius:50%;background:#2f3d45;border:3px solid #e6eef2}
.avatar.current{background:#d6e2e8}

/* footer */
.site-footer{left:0;top:2099px;width:1200px;height:282px;background:var(--footer-bg)}
.footer-col{top:48px;width:300px}
.footer-col h4{font-family:"Raleway",sans-serif;font-weight:600;font-size:17px;color:var(--brand);margin-bottom:16px}
.footer-col li{list-style:none;font-size:12px;color:#8f8f8f;line-height:28px;padding-left:14px;position:relative}
.footer-col li::before{content:"";position:absolute;left:0;top:13px;width:4px;height:4px;border-radius:50%;background:#bbb}
.footer-col li b{color:var(--brand)}
.footer-col .more{display:block;font-size:12px;font-weight:700;color:var(--brand);margin:6px 0 0 10px}
.divider{top:38px;width:1px;height:205px;background:#d8dedc}

.bottom-bar{left:0;top:2381px;width:1200px;height:95px;background:var(--brand-deep)}
.copyright{left:46px;top:38px;color:#eee;font-size:12px}
.social{top:30px;width:30px;height:30px;border:1.5px solid #fff}
</style>
</head>
<body>

<header class="site-header abs">
  <div class="brand abs">
    <div class="brand-mark"></div>
    <div class="brand-name">Pine Hollow Imaging Partners</div>
  </div>
  <div class="contact-box abs" style="left:482px;width:168px"><b>Medical Records:</b><span>☎ (555) 210-4471</span></div>
  <div class="contact-box abs" style="left:663px;width:157px"><b>Billing:</b><span>☎ (555) 210-4482</span></div>
  <div class="contact-box abs" style="left:833px;width:157px"><b>Scheduling:</b><span>☎ (555) 210-4493</span></div>
  <div class="contact-box abs" style="left:1004px;width:151px"><b>Main Line:</b><span>☎ (555) 210-4400</span></div>
</header>

<nav class="main-nav abs">
  <a class="active" href="#">Home</a><a href="#">About Us</a><a href="#">Our Service</a><a href="#">For Patients</a><a href="#">Our Physicians</a><a href="#">For Physicians</a><a href="#">PACS &amp; Document</a><a href="#">Appointment</a><a href="#">Our Location</a>
</nav>

<section class="hero abs" role="img" aria-label="Photo of a family walking a snowy pine trail under a clear spring sky in the high desert"></section>
<div class="hero-panel abs">
  <h1>Welcome to Pine Hollow<br>Imaging Partners</h1>
  <p>Friendly, expert imaging close to home. Our radiologists and technologists take time to explain every step, so you feel comfortable, informed and cared for from check-in to results.</p>
</div>
<div class="dots abs"><i></i><i></i><i class="on"></i><i></i><i></i></div>
<a class="btn hero-btn abs" href="#">Read More</a>

<section class="actions abs">
  <div class="action"><div class="action-icon"><svg width="32" height="36" viewBox="0 0 32 36" fill="none" stroke="#fff" stroke-width="2.5"><path d="M4 2h16l8 8v24H4z"/><path d="M10 16h12M10 22h12M10 28h8"/></svg></div>Patient Bill<br>Pay</div>
  <div class="action"><div class="action-icon"><svg width="34" height="34" viewBox="0 0 34 34" fill="none" stroke="#fff" stroke-width="2.5"><circle cx="17" cy="17" r="14"/><path d="M17 9v9h7"/></svg></div>Make an<br>Appointment</div>
  <div class="action"><div class="action-icon"><svg width="32" height="34" viewBox="0 0 32 34" fill="#fff"><circle cx="16" cy="10" r="7"/><path d="M3 33c0-9 6-14 13-14s13 5 13 14z"/></svg></div>Meet Our<br>Doctors</div>
  <div class="action"><div class="action-icon"><svg width="26" height="36" viewBox="0 0 26 36" fill="#fff"><path d="M13 1C6 1 1 6 1 13c0 9 12 22 12 22s12-13 12-22C25 6 20 1 13 1z"/><circle cx="13" cy="13" r="4.5" fill="#3d7ea6"/></svg></div>Find a<br>Location</div>
  <div class="action"><div class="action-icon"><svg width="30" height="36" viewBox="0 0 30 36" fill="#fff"><path d="M3 4h24v31H3z"/><g fill="#3d7ea6"><rect x="8" y="9" width="4" height="4"/><rect x="18" y="9" width="4" height="4"/><rect x="8" y="17" width="4" height="4"/><rect x="18" y="17" width="4" height="4"/><rect x="12" y="26" width="6" height="9"/></g></svg></div>Events &amp;<br>Classes</div>
  <div class="action"><div class="action-icon"><svg width="32" height="34" viewBox="0 0 32 34" fill="#fff"><circle cx="16" cy="10" r="8"/><path d="M2 33c0-9 6-14 14-14s14 5 14 14z"/></svg></div>Customer<br>Care</div>
  <div class="action"><div class="action-icon"><svg width="36" height="32" viewBox="0 0 36 32" fill="none" stroke="#fff" stroke-width="2.5"><path d="M3 4h22v14H12l-6 5v-5H3z"/><path d="M28 10h5v13h-3v5l-6-5H13v-2"/></svg></div>Patient<br>Testimonials</div>
</section>

<section class="welcome abs">
  <h2>Welcome to <em>Pine Hollow Imaging Partners</em></h2>
  <p>For more than thirty years our board-certified radiologists have served families across the high desert with accurate, timely imaging. We offer MRI, CT, ultrasound, mammography and X-ray in calm, welcoming clinics, with same-week appointments and results shared quickly with you and your doctor. Whether it is a routine screening or a complex study, our team is here to answer questions and make your visit as easy as possible.</p>
  <a class="btn" href="#">READ MORE</a>
</section>

<section class="services abs" role="img" aria-label="Darkened photo of a pine forest at dusk behind the services list">
  <h2 class="section-title">Our <em>Service</em></h2>
</section>
<div class="spine abs"></div>
<div class="spine-h abs" style="top:1286px"></div>
<div class="spine-h abs" style="top:1436px"></div>
<div class="spine-h abs" style="top:1601px"></div>

<div class="service-photo abs" style="left:442px;top:1230px;background:#2f5f8f" role="img" aria-label="Illustration of the colon"></div>
<div class="service-photo abs" style="left:442px;top:1380px;background:#6e7072" role="img" aria-label="Mammogram image"></div>
<div class="service-photo abs" style="left:442px;top:1545px;background:#c9d3d8" role="img" aria-label="Photo of an ultrasound probe in use"></div>
<div class="service-photo abs" style="left:637px;top:1230px;background:#a9bcc6" role="img" aria-label="Photo of an MRI scanner"></div>
<div class="service-photo abs" style="left:637px;top:1380px;background:#b8cdd8" role="img" aria-label="Photo of a CT scanner"></div>
<div class="service-photo abs" style="left:637px;top:1545px;background:#9fb9c6" role="img" aria-label="Photo of an x-ray room"></div>

<div class="service left abs" style="top:1236px"><h3>Virtual Colonoscopy (VC)</h3><p>A gentle, minimally invasive scan of the colon that needs no sedation and lets you get back to your day quickly.</p><a href="#">READ MORE ▸</a></div>
<div class="service left abs" style="top:1383px"><h3>Digital Mammography</h3><p>Low-dose 3D breast imaging with caring female technologists and results reviewed by specialist breast radiologists.</p><a href="#">READ MORE ▸</a></div>
<div class="service left abs" style="top:1543px"><h3>Ultrasound</h3><p>Safe, radiation-free imaging using sound waves, ideal for pregnancy, abdominal, vascular and joint exams.</p><a href="#">READ MORE ▸</a></div>
<div class="service right abs" style="top:1236px"><h3>Magnetic Resonance Imaging (MRI)</h3><p>Detailed images of joints, brain and soft tissue in a wide-bore scanner designed for extra comfort.</p><a href="#">READ MORE ▸</a></div>
<div class="service right abs" style="top:1383px"><h3>Computed Tomography (CT)</h3><p>Fast, low-dose scans that give your doctor clear cross-sectional views; most exams take only minutes.</p><a href="#">READ MORE ▸</a></div>
<div class="service right abs" style="top:1543px"><h3>General Radiography</h3><p>Walk-in X-ray for bones, chest and more, with no appointment needed at most of our locations.</p><a href="#">READ MORE ▸</a></div>

<section class="testimonials abs">
  <h2 class="section-title">Client Testimonials</h2>
  <p class="quote"><span class="mark">“</span> The staff made me feel at ease from the moment I walked in. Everything was explained clearly,<br>and my results reached my doctor the very next day.<span class="mark">”</span></p>
  <p class="author">- MARION TEAGUE</p>
  <div class="avatars">
    <div class="avatar" role="img" aria-label="Client portrait"></div>
    <div class="avatar" role="img" aria-label="Client portrait"></div>
    <div class="avatar current" role="img" aria-label="Client portrait"></div>
    <div class="avatar" role="img" aria-label="Client portrait"></div>
  </div>
</section>

<footer class="site-footer abs">
  <div class="footer-col abs" style="left:53px"><h4>For Patients</h4><ul><li>About Your Visit</li><li>Why Choose Us?</li><li>Patient Forms</li><li>Billing and Insurance</li></ul><span class="more">More +</span></div>
  <div class="divider abs" style="left:329px"></div>
  <div class="footer-col abs" style="left:360px"><h4>Quick Links</h4><ul><li>About Us</li><li>Our Physicians</li><li>For Physicians</li><li>Disclaimer</li></ul><span class="more">More +</span></div>
  <div class="divider abs" style="left:610px"></div>
  <div class="footer-col abs" style="left:640px;top:43px"><h4>Our Services</h4><ul><li>Mammography</li><li>MRI</li><li>CT-64</li><li>X-Ray</li></ul><span class="more">More +</span></div>
  <div class="divider abs" style="left:893px"></div>
  <div class="footer-col abs" style="left:926px"><h4>Contact Us</h4><ul><li>(555) 210-4400 - <b>Main Line</b></li><li>(555) 210-4493 - <b>Scheduling</b></li><li>(555) 210-4482 - <b>Billing</b></li><li>(555) 210-4471 - <b>Medical Records</b></li></ul></div>
</footer>

<div class="bottom-bar abs">
  <p class="copyright abs">Copyright 2016 Company Name.  All Rights Reserved.</p>
  <div class="social abs" style="left:1038px"></div>
  <div class="social abs" style="left:1082px"></div>
  <div class="social abs" style="left:1124px"></div>
</div>

</body>
</html>
```